Animal Eye Clinic needs a Business card

We are a new veterinary ophthalmology practice (Ridgeline Pet Vision Care) and we need a business card designed. We only see animal eyes - we are not a regular veterinary clinic. We already have a logo. We are looking for a professional, good looking business card to hand out to our clients. We are looking for something simple but professional and contemporary. Our logo is likely the only picture/graphic that needs to be on the card.
Updates

Contact Information for Business Card

Delia Vossman, DVM, PhD, DipACVO
Veterinary Ophthalmologist

Phone: 250.418.3927
Email: ridgelinepetvisioncare@mailbox-example.net
Website: ridgelinepetvisioncare-example.net
Address: 1874 Thornbury Rd
Cedarholm, BC, V1X 4M9

Colors

Designer to choose colors to be used in the design.

Requirements
Must have
• Our logo (attached)

```html
<!DOCTYPE html>
<html lang="en">
<head>
<meta charset="utf-8">
<title>Ridgeline Pet Vision Care – Business Card</title>
<link href="https://fonts.googleapis.com/css2?family=Roboto:wght@300;400;500&display=swap" rel="stylesheet">
<style>
  :root {
    --teal: #12b3bf;
    --teal-dark: #0796a3;
    --teal-light: #22c6cf;
    --grey-band: #a9abae;
    --paper: #f4f5f6;
    --paper-shade: #e3e4e6;
    --white: #ffffff;
    --stage: #e9eaec;
  }
  * { box-sizing: border-box; margin: 0; padding: 0; }
  html, body {
    width: 1200px; height: 780px; overflow: hidden;
    background: var(--stage);
    font-family: "Roboto", Arial, sans-serif;
  }
  .stage {
    width: 1200px; height: 780px;
    display: flex; align-items: center; justify-content: center; gap: 40px;
  }
  .card {
    position: relative;
    width: 540px; height: 309px;
    overflow: hidden;
    box-shadow: 0 10px 24px rgba(0,0,0,.18);
  }

  /* Front */
  .card-front { background: linear-gradient(180deg, var(--white), var(--paper) 50%, var(--paper-shade)); }
  .card-front .bands { position: absolute; inset: 0; }
  .brand {
    position: absolute; left: 30px; top: 40px;
    display: flex; align-items: center; gap: 14px;
  }
  .brand-dot {
    flex: none;
    width: 46px; height: 46px; border-radius: 50%;
    background: var(--teal);
  }
  .brand-name {
    color: var(--teal);
    font-weight: 500; font-size: 22px; line-height: 1.15;
    letter-spacing: .5px; text-transform: uppercase;
  }
  .person {
    position: absolute; left: 30px; top: 150px;
    color: var(--white);
  }
  .person-name { font-size: 16px; font-weight: 400; white-space: nowrap; }
  .person-title { font-size: 12px; font-weight: 300; margin-top: 2px; }
  .contact {
    position: absolute; left: 30px; top: 206px;
    color: var(--white); font-size: 12px; font-weight: 300; line-height: 1.5;
    list-style: none;
  }
  .contact li { display: flex; align-items: center; gap: 7px; white-space: nowrap; }
  .contact .address { display: block; margin-bottom: 4px; }
  .icon {
    flex: none;
    width: 14px; height: 14px; border-radius: 50%;
    background: var(--white); display: inline-flex; align-items: center; justify-content: center;
  }

  /* Back */
  .card-back {
    background: radial-gradient(ellipse at 35% 30%, var(--teal-light), var(--teal) 55%, var(--teal-dark));
    display: flex; align-items: center; justify-content: center;
  }
  .back-brand { display: flex; align-items: center; gap: 16px; }
  .back-brand .brand-dot { background: var(--white); width: 54px; height: 54px; }
  .back-brand .brand-name { color: var(--white); font-size: 26px; }
</style>
</head>
<body>
<main class="stage">

  <section class="card card-front" aria-label="Business card front">
    <svg class="bands" width="540" height="309" viewBox="0 0 540 309" aria-hidden="true">
      <polygon points="0,140 340,140 540,40 540,309 0,309" fill="#12b3bf"/>
      <polygon points="0,140 340,140 540,40 540,62 350,198 0,198" fill="#a9abae"/>
    </svg>

    <div class="brand">
      <span class="brand-dot"></span>
      <div class="brand-name">Ridgeline<br>Pet Vision Care</div>
    </div>

    <div class="person">
      <p class="person-name">Delia Vossman, DVM, PhD, DipACVO</p>
      <p class="person-title">Veterinary Ophthalmologist</p>
    </div>

    <ul class="contact">
      <li class="address">1874 Thornbury Rd<br>Cedarholm, BC, V1X 4M9</li>
      <li>
        <span class="icon"><svg width="8" height="8" viewBox="0 0 10 10"><path d="M2 1 L4 1 L4.6 3 L3.4 3.8 Q4.5 6 6.2 6.6 L7 5.4 L9 6 L9 8 Q9 9 8 9 Q1 8.5 1 2 Q1 1 2 1Z" fill="#12b3bf"/></svg></span>
        250.418.3927
      </li>
      <li>
        <span class="icon"><svg width="8" height="8" viewBox="0 0 10 10"><rect x="1" y="2.5" width="8" height="5.5" fill="none" stroke="#12b3bf" stroke-width="1.2"/><path d="M1 2.5 L5 5.6 L9 2.5" fill="none" stroke="#12b3bf" stroke-width="1.2"/></svg></span>
        ridgelinepetvisioncare@mailbox-example.net
      </li>
    </ul>
  </section>

  <section class="card card-back" aria-label="Business card back">
    <div class="back-brand">
      <span class="brand-dot"></span>
      <div class="brand-name">Ridgeline<br>Pet Vision Care</div>
    </div>
  </section>

</main>
</body>
</html>
```